KRT Project Signage

Need a sign to be displayed in the front of properties currently under Construction or Renovation to advertise our company information. Need it to be Professional and Contemporary. We are a Design/Build Construction Company. Information should include Company Name, email, website, phone number. Attached: Logo and company brochure, also included and inspiration images

```html
<!DOCTYPE html>
<html lang="en">
<head>
<meta charset="utf-8">
<title>KRT Project Signage</title>
<link rel="stylesheet" href="https://fonts.googleapis.com/css2?family=Poppins:wght@400;500;600;700;800&display=swap">
<style>
  :root {
    --backdrop: #9aa1a8;
    --sign-white: #ffffff;
    --brand-yellow: #f2ea42;
    --brand-black: #000000;
    --ink-dark: #0f1d22;
  }
  html, body {
    margin: 0;
    padding: 0;
    width: 1200px;
    height: 2400px;
    overflow: hidden;
    background: var(--backdrop);
  }
  .canvas {
    position: relative;
    width: 1200px;
    height: 2400px;
  }
  .project-sign {
    position: absolute;
    left: 60px;
    top: 390px;
    width: 1080px;
    height: 1620px;
    box-shadow: 0 18px 40px rgba(0, 0, 0, 0.35);
  }
  .project-sign svg {
    display: block;
    width: 100%;
    height: 100%;
  }
  .sign-text {
    font-family: "Poppins", sans-serif;
  }
  .company-name { fill: var(--ink-dark); font-weight: 500; font-size: 88px; }
  .company-tagline { fill: var(--ink-dark); font-weight: 500; font-size: 34px; letter-spacing: 10px; }
  .contact-line { fill: var(--sign-white); font-weight: 500; font-size: 38px; }
  .contact-email { fill: var(--sign-white); font-weight: 500; font-size: 40px; }
  .office-label { fill: var(--brand-black); font-weight: 800; font-size: 42px; letter-spacing: 4px; }
  .office-number { fill: var(--brand-black); font-weight: 700; font-size: 56px; }
  .mobile-number { fill: var(--sign-white); font-weight: 700; font-size: 88px; }
  .footer-name { fill: var(--brand-black); font-weight: 500; font-size: 38px; }
</style>
</head>
<body>
<main class="canvas">
  <section class="project-sign" aria-label="Marcus Hale Design and Builder project sign">
    <svg viewBox="0 0 778 1166" xmlns="http://www.w3.org/2000/svg">
      <!-- background panels -->
      <rect class="panel-white" width="778" height="1166" fill="var(--sign-white)"/>
      <polygon class="band-top" points="0,50 390,300 778,183 778,228 390,334 0,228" fill="var(--brand-yellow)"/>
      <polygon class="panel-black" points="0,228 390,334 778,228 778,838 390,827 0,942" fill="var(--brand-black)"/>
      <polygon class="band-bottom" points="0,942 390,827 778,838 778,1097 390,892 0,980" fill="var(--brand-yellow)"/>

      <!-- header -->
      <text class="sign-text company-name" x="389" y="155" text-anchor="middle" textLength="640" lengthAdjust="spacingAndGlyphs">MARCUS HALE</text>
      <text class="sign-text company-tagline" x="389" y="212" text-anchor="middle">DESIGN &amp; BUILDER</text>

      <!-- address -->
      <g class="icon-pin" transform="translate(392,342)">
        <circle r="27" fill="var(--brand-yellow)"/>
        <path d="M0,-15 a11,11 0 0 1 11,11 c0,8 -11,19 -11,19 c0,0 -11,-11 -11,-19 a11,11 0 0 1 11,-11 z" fill="var(--brand-black)"/>
        <circle cy="-4" r="4.5" fill="var(--brand-yellow)"/>
      </g>
      <text class="sign-text contact-line" x="392" y="414" text-anchor="middle">1480 Harbor View Rd., Ste. 310</text>
      <text class="sign-text contact-line" x="392" y="460" text-anchor="middle">Coral Bay, FL 33102</text>

      <!-- email -->
      <g class="icon-mail" transform="translate(392,524)">
        <circle r="27" fill="var(--brand-yellow)"/>
        <rect x="-15" y="-10" width="30" height="20" rx="2" fill="var(--brand-black)"/>
        <polyline points="-13,-8 0,3 13,-8" fill="none" stroke="var(--brand-yellow)" stroke-width="2"/>
      </g>
      <text class="sign-text contact-email" x="392" y="587" text-anchor="middle">mark@krtconstruction.com</text>

      <!-- office number -->
      <rect class="office-pill" x="68" y="638" width="260" height="71" rx="12" fill="var(--sign-white)"/>
      <rect class="office-pill-number" x="310" y="638" width="405" height="71" rx="12" fill="var(--brand-yellow)"/>
      <text class="sign-text office-label" x="98" y="692">OFFICE</text>
      <g class="icon-phone-office" transform="translate(311,674)">
        <circle r="27" fill="var(--brand-black)"/>
        <path d="M-11,-13 l6,-2 l5,9 l-4,4 c2,5 5,8 10,10 l4,-4 l9,5 l-2,6 c-16,2 -30,-12 -28,-28 z" fill="var(--sign-white)"/>
      </g>
      <text class="sign-text office-number" x="350" y="693" textLength="340" lengthAdjust="spacingAndGlyphs">555.214.3090</text>

      <!-- mobile number -->
      <g class="icon-phone-mobile" transform="translate(112,770)">
        <circle r="33" fill="var(--brand-yellow)"/>
        <path d="M-14,-16 l7,-3 l6,11 l-5,5 c3,6 6,9 12,12 l5,-5 l11,6 l-3,7 c-20,3 -36,-13 -33,-33 z" fill="var(--brand-black)"/>
      </g>
      <text class="sign-text mobile-number" x="165" y="800" textLength="555" lengthAdjust="spacingAndGlyphs">555.308.7724</text>

      <!-- footer company name with plain marker -->
      <g class="footer-brand">
        <text class="sign-text footer-name" x="108" y="1022">KRT CONSTRUCTION</text>
        <circle class="footer-dot" cx="550" cy="1009" r="22" fill="var(--brand-yellow)"/>
      </g>
    </svg>
  </section>
</main>
</body>
</html>
```